Nanny Share Ecommerce Website for Finding Childcare and Parents who need Childcare BrightPramHub.net

Our company needs an ecommerce website (BrightPramHub.net) for a US subscription based service strictly for nanny sharing that connects families and caregivers. The website would allow families to connect with one another as well as to search for nannies. The service would be searchable for other families by location (by radius or zip code), children demographic (age range/gender/special needs), days of week or times, after school care, school closure days (holidays), etc. The service would also be searchable for nannies based on gender, provider age range, years experience, language, hourly rate, transportation available, certification (CPR first aid), education etc. The search fields would be searchable and sortable and allow to connect with the provider (after paying subscription fee). The service would be similar to tendlyfolk.net in that it would allow for families and caregivers to post photos as well as a short bio of the themselves. There would also be a feedback/star rating mechanism to rate caregivers who have performed work for families (viewable to public). The service would be free for nannies to post their bios and only a subscription based service for families to connect with other families or with caregivers (able to view bio but need service to connect). There will be a short bio on the benefits of nanny sharing (reduced cost, increased flexibility for parents, reduced illness, increased socialization with other children vs. sole nanny), as well as Q&A section with best practices.

Target Market(s)

Families, Nannies

Industry/Entity Type

Childcare

Logo Text

Bright Pram Hub

Coding

Coded - Design and coding required

Number of Pages Required

5+ page

Requirements
Must have
• Searchable (need to be able to search for families as well as nannies), responsive, functional, easy to use, add value to families and nannies. Needs to be able to collect payment for subscription.
Nice to have
• Optimized for mobile, SEO optimized

```html
<!DOCTYPE html>
<html lang="en">
<head>
<meta charset="utf-8">
<title>Bright Pram Hub</title>
<link href="https://fonts.googleapis.com/css2?family=Fredoka:wght@500;600&family=Open+Sans:ital,wght@0,400;0,600;0,700;1,400&display=swap" rel="stylesheet">
<style>
:root{
  --cyan:#1fc1e0;
  --pink:#f06292;
  --pink-soft:#f7a8c2;
  --ink:#2b2b2b;
  --text:#666;
  --muted:#9a9a9a;
  --line:#e3e3e3;
  --strip:#f4f4f4;
  --footer:#2d2d2d;
  --white:#fff;
}
*{box-sizing:border-box;margin:0;padding:0}
html,body{width:1200px;height:3871px;overflow:hidden;background:var(--white)}
body{font-family:"Open Sans",Arial,sans-serif;color:var(--text);position:relative}
section,header,footer{position:absolute;left:0;width:1200px}
.abs{position:absolute}
h1,h2,h3,h4{font-family:"Fredoka",Arial,sans-serif;color:var(--ink)}

/* header */
.site-header{top:0;height:103px;background:var(--white);box-shadow:0 1px 4px rgba(0,0,0,.06);z-index:2}
.brand{left:98px;top:34px;display:flex;align-items:center;gap:10px;font-family:"Open Sans",sans-serif;font-weight:700;font-size:24px;color:var(--ink)}
.brand-dot{width:26px;height:26px;border-radius:50%;background:var(--pink)}
.nav{left:480px;top:42px;display:flex;font-size:14px;color:#444}
.nav a{color:inherit;text-decoration:none;margin-right:50px}
.nav a.active{color:var(--cyan)}
.nav-search{left:1086px;top:42px}

/* hero */
.hero{top:103px;height:550px}
.hero-photo{inset:0;background:linear-gradient(90deg,#c69a82 0%,#e2c2b0 25%,#e9e2dc 48%,#eeeeee 62%,#f2f2f2 100%)}
.hero-title{left:684px;top:188px;font-size:48px;font-weight:600}
.hero-sub{left:686px;top:264px;font-size:15px;color:#555}
.btn{display:inline-flex;align-items:center;justify-content:center;border-radius:22px;font-size:13px;font-weight:600;letter-spacing:.3px;text-transform:uppercase}
.btn-cyan{background:var(--cyan);color:#fff}
.btn-pink-line{border:2px solid var(--pink);color:var(--pink)}
.hero .btn{top:308px;height:42px}
.arrow-btn{width:32px;height:32px;border-radius:50%;background:rgba(255,255,255,.85);display:flex;align-items:center;justify-content:center;box-shadow:0 1px 3px rgba(0,0,0,.15)}

/* testimonial */
.testimonial{top:653px;height:167px;background:var(--strip)}
.avatar{left:113px;top:24px;width:120px;height:120px;border-radius:50%;background:linear-gradient(135deg,#c9b8a8,#e9ddd2);border:4px solid #fff}
.quote-badge{left:200px;top:100px;width:38px;height:38px;border-radius:50%;background:var(--pink);color:#fff;font-size:26px;font-weight:700;display:flex;align-items:center;justify-content:center;font-family:Georgia,serif}
.testimonial p{left:264px;top:26px;width:820px;font-size:13.5px;font-style:italic;line-height:26px;color:#888}
.byline{left:264px;top:110px;font-weight:700;font-size:18px;color:#444;display:flex;align-items:center;gap:12px}
.stars{color:#f2b01e;font-size:18px;letter-spacing:2px}

/* section titles */
.section-title{left:0;width:1200px;text-align:center;font-size:38px;font-weight:600;display:flex;justify-content:center;align-items:center;gap:26px}
.section-title::before,.section-title::after{content:"";width:100px;height:1px;background:var(--line)}
.section-title.light{color:#fff}
.section-title.light::before,.section-title.light::after{background:rgba(255,255,255,.6)}

/* services */
.services{top:820px;height:736px}
.service-circle{width:202px;height:202px;border-radius:50%;border:6px solid #fff;box-shadow:0 2px 8px rgba(0,0,0,.15)}
.service-text{width:250px}
.service-text h3{font-family:"Open Sans",sans-serif;font-weight:600;font-size:21px;color:var(--ink);margin-bottom:10px}
.service-text p{font-size:13.5px;line-height:25px;color:#888}
.service-text.left{text-align:right;left:102px}
.service-text.right{left:849px}
.pill-sm{height:30px;padding:0 20px;border:1.5px solid var(--pink);color:var(--pink);border-radius:16px;font-size:11px;font-weight:600;display:inline-flex;align-items:center;margin-top:14px;text-transform:uppercase}

/* about */
.about{top:1556px;height:555px;background:linear-gradient(100deg,#f07a9e 0%,#d68bb5 30%,#9bb0dc 60%,#4cc8ea 100%)}
.about-title{left:98px;top:100px;display:flex;align-items:center;gap:20px;font-size:38px;color:#fff;font-weight:600}
.about-title::before,.about-title::after{content:"";width:60px;height:1px;background:rgba(255,255,255,.7)}
.about-copy{left:98px;top:162px;width:510px;color:#fff;font-size:12.5px;line-height:24px}
.about-copy p+p{margin-top:10px}
.btn-white-line{left:98px;top:415px;height:42px;width:150px;border:2px solid #fff;color:#fff}
.about-photo{left:642px;top:113px;width:460px;height:333px;border:6px solid #fff;background:linear-gradient(135deg,#b59a84,#d9c6b5 55%,#8d7a6a)}

/* faq */
.faq{top:2111px;height:580px}
.faq-list{left:163px;top:167px;width:872px}
.faq-item{height:40px;border:1px solid var(--line);display:flex;align-items:center;padding:0 16px;font-size:13.5px;color:#555;margin-bottom:14px;justify-content:space-between}
.faq-item .q{color:var(--pink);font-weight:700;margin-right:6px}
.faq-item.open{background:var(--pink);border-color:var(--pink);color:#fff;margin-bottom:0}
.faq-item.open .q{color:#fff}
.faq-answer{border:1px solid var(--line);border-top:0;padding:12px 26px;font-size:12px;line-height:22px;color:#888;height:70px;margin-bottom:38px}
.plus{width:14px;height:14px;border-radius:50%;background:#bbb;color:#fff;font-size:12px;line-height:14px;text-align:center;font-weight:700}
.faq-item.open .plus{background:#fff;color:var(--pink)}

/* how it works */
.how{top:2691px;height:405px;background:linear-gradient(100deg,#f07a9e 0%,#c993bd 40%,#72bde6 70%,#22c0e8 100%)}
.step{width:180px;text-align:center;color:#fff;font-size:19px}
.step-icon{width:103px;height:103px;border-radius:50%;background:#fff;border:5px solid rgba(255,255,255,.5);background-clip:padding-box;margin:0 auto 20px;display:flex;align-items:center;justify-content:center}
.dash{height:0;border-top:2px dashed rgba(255,255,255,.8);top:228px}

/* benefits */
.benefits{top:3096px;height:516px}
.benefit{width:320px;text-align:center}
.benefit h4{font-family:"Open Sans",sans-serif;font-weight:600;font-size:17px;color:#444;margin:10px 0 8px}
.benefit p{font-size:13px;line-height:22px;color:#888}
.btn-pink{background:var(--pink);color:#fff;height:42px;width:148px;left:526px;top:408px}
.side-arrow{font-size:26px;color:#444;top:285px}

/* footer */
.site-footer{top:3612px;height:259px;background:var(--footer);border-top:4px solid var(--cyan)}
.socials{left:0;width:1200px;top:30px;display:flex;justify-content:center;gap:6px}
.social{width:36px;height:36px;border-radius:50%;border:1.5px solid #fff}
.footer-nav{left:0;width:1200px;top:132px;text-align:center;color:#fff;font-size:13px}
.footer-nav span{margin:0 10px;color:#bbb}
.copyright{left:0;width:1200px;top:176px;text-align:center;color:#ddd;font-size:12px}
</style>
</head>
<body>

<header class="site-header">
  <div class="abs brand"><span class="brand-dot"></span>Bright Pram Hub</div>
  <nav class="abs nav">
    <a class="active" href="#">Home</a><a href="#">About us</a><a href="#">Services</a><a href="#">Feedbacks</a><a href="#">FAQ</a><a href="#">Contact us</a>
  </nav>
  <svg class="abs nav-search" width="16" height="16" viewBox="0 0 16 16"><circle cx="6.5" cy="6.5" r="4.5" fill="none" stroke="#f06292" stroke-width="2"/><line x1="10" y1="10" x2="14" y2="14" stroke="#f06292" stroke-width="2"/></svg>
</header>

<section class="hero">
  <div class="abs hero-photo" role="img" aria-label="Photo of a mother and a young girl stacking colourful toy blocks at a table"></div>
  <h1 class="abs hero-title">Bright Pram Hub</h1>
  <p class="abs hero-sub">Sed ut perspiciatis unde omnis iste natus error sit voluptatem</p>
  <span class="abs btn btn-cyan" style="left:684px;width:147px">Find care</span>
  <span class="abs btn btn-pink-line" style="left:840px;width:222px">Search for nannies</span>
  <div class="abs arrow-btn" style="left:22px;top:262px"><svg width="10" height="12"><path d="M8 1L2 6l6 5" fill="none" stroke="#555" stroke-width="2"/></svg></div>
  <div class="abs arrow-btn" style="left:1146px;top:262px"><svg width="10" height="12"><path d="M2 1l6 5-6 5" fill="none" stroke="#555" stroke-width="2"/></svg></div>
</section>

<section class="testimonial">
  <svg class="abs" style="left:62px;top:74px" width="12" height="18"><path d="M10 2L3 9l7 7" fill="none" stroke="#333" stroke-width="2.5"/></svg>
  <div class="abs avatar" role="img" aria-label="Portrait photo of a smiling senior woman"></div>
  <div class="abs quote-badge">”</div>
  <p class="abs">At vero eos et accusamus et iusto odio dignissimos excepturi sint ocinos duccaecati cupiditate non provicimus qui blanditiis praesentium voluptatum deleniti atque corrupti quos dolores et quas molestias excepturi sint occaecati cupiditate non provident, similique sunt in culpa qui officia deserunt mollitia animid est laborum et dolorum fuga.</p>
  <div class="abs byline">- Laborious <span class="stars">★★★★☆</span></div>
  <svg class="abs" style="left:1120px;top:74px" width="12" height="18"><path d="M2 2l7 7-7 7" fill="none" stroke="#333" stroke-width="2.5"/></svg>
</section>

<section class="services">
  <h2 class="abs section-title" style="top:90px">Our Services</h2>
  <div class="abs service-text left" style="top:212px"><h3>Child Care</h3><p>Sed ut perspiciatis unde omnis iste natus error sit voluptatem accusantium doloremque laudantiumre aae</p><span class="pill-sm">Read more</span></div>
  <div class="abs service-circle" style="left:379px;top:191px;background:linear-gradient(135deg,#e7b9a6,#f3e2d8 60%,#c79c86)" role="img" aria-label="Photo of a caregiver reading with a little girl"></div>
  <div class="abs service-circle" style="left:622px;top:191px;background:linear-gradient(135deg,#d8c1b0,#f1e6de 60%,#b9a08e)" role="img" aria-label="Photo of a carer embracing a senior woman"></div>
  <div class="abs service-text right" style="top:212px"><h3>Adult &amp; Senior care</h3><p>Sed ut perspiciatis unde omnis iste natus error sit voluptatem accusantium doloremque laudantiumre aae</p><span class="pill-sm">Read more</span></div>
  <div class="abs service-text left" style="top:456px"><h3>Pet Care</h3><p>Sed ut perspiciatis unde omnis iste natus error sit voluptatem accusantium doloremque laudantiumre aae</p><span class="pill-sm">Read more</span></div>
  <div class="abs service-circle" style="left:379px;top:436px;background:linear-gradient(135deg,#8a5a3a,#c79a6c 55%,#e9d8c4)" role="img" aria-label="Photo of a puppy resting in a wicker basket"></div>
  <div class="abs service-circle" style="left:622px;top:436px;background:linear-gradient(135deg,#efe9e2,#c9b6a2 55%,#a67c52)" role="img" aria-label="Photo of a bright tidy living room"></div>
  <div class="abs service-text right" style="top:456px"><h3>Home Care</h3><p>Sed ut perspiciatis unde omnis iste natus error sit voluptatem accusantium doloremque laudantiumre aae</p><span class="pill-sm">Read more</span></div>
</section>

<section class="about">
  <h2 class="abs about-title">About Us</h2>
  <div class="abs about-copy">
    <p>At vero eos et accusamus et iusto odio dignissimos ducimus qui blanditiis praesentium voluptatum deleniti atque corrupti quos dolores et quas molestias excepturi sint occaecati cupiditate non provident, similique sunt in culpa qui officia deserunt mollitia animi, id est laborum et dolorum fuga. Et harum quidem rerum facilis est et expedita distinctio. Nam libero tempore, cum soluta nobis est eligendi optio cumque nihil impedit quo minus id quod maxime placeat facere possimus.</p>
    <p>Et harum quidem rerum facilis est et expedita distinctio. Nam libero tempore, cum soluta nobis est eligendi optio cumque nihil impedit quo minus id quod maxime.</p>
  </div>
  <span class="abs btn btn-white-line">Read more</span>
  <div class="abs about-photo" role="img" aria-label="Photo of a mother and daughter playing on the floor with a dog"></div>
</section>

<section class="faq">
  <h2 class="abs section-title" style="top:84px">Frequently asked Questions</h2>
  <div class="abs faq-list">
    <div class="faq-item open"><span><span class="q">Q.</span>How do placeat facere possimus, omnis voluptas assumen?</span><span class="plus">–</span></div>
    <div class="faq-answer">Nam libero tempore, cum soluta nobis est eligendi optio cumque nihil impedit apretur a sapiente delectus minus id quod maxime placeat facere possimusretur a sapiente delect.</div>
    <div class="faq-item"><span><span class="q">Q.</span>If arum facilis est et expedita distin?</span><span class="plus">+</span></div>
    <div class="faq-item"><span><span class="q">Q.</span>If aro eos et accusamus et iusto odio?</span><span class="plus">+</span></div>
    <div class="faq-item"><span><span class="q">Q.</span>Where again is there anyone who loves?</span><span class="plus">+</span></div>
    <div class="faq-item"><span><span class="q">Q.</span>Why facilis est et expedita distin?</span><span class="plus">+</span></div>
  </div>
</section>

<section class="how">
  <h2 class="abs section-title light" style="top:90px">How it Works</h2>
  <div class="abs dash" style="left:220px;width:100px"></div>
  <div class="abs dash" style="left:434px;width:92px"></div>
  <div class="abs dash" style="left:640px;width:105px"></div>
  <div class="abs dash" style="left:859px;width:95px"></div>
  <div class="abs step" style="left:73px;top:177px"><div class="step-icon"><svg width="40" height="40" viewBox="0 0 40 40" fill="none" stroke="#1fc1e0" stroke-width="3"><rect x="6" y="10" width="22" height="24" rx="2"/><path d="M18 24l14-14 3 3-14 14h-3z"/></svg></div>Sign up</div>
  <div class="abs step" style="left:287px;top:177px"><div class="step-icon"><svg width="40" height="40" viewBox="0 0 40 40" fill="none" stroke="#1fc1e0" stroke-width="3"><path d="M10 4h14l8 8v24H10z"/><path d="M15 18h12M15 24h12M15 30h8"/></svg></div>Create a job</div>
  <div class="abs step" style="left:493px;top:177px"><div class="step-icon"><svg width="40" height="40" viewBox="0 0 40 40"><path d="M20 4l5 11 12 1-9 8 3 12-11-7-11 7 3-12-9-8 12-1z" fill="#1fc1e0"/></svg></div>Review profiles</div>
  <div class="abs step" style="left:712px;top:177px"><div class="step-icon"><svg width="40" height="40" viewBox="0 0 40 40" fill="none" stroke="#1fc1e0" stroke-width="3"><rect x="5" y="17" width="7" height="17"/><path d="M12 19l7-13c4 0 4 4 3 9h10c2 0 3 2 2 4l-4 13c-1 2-2 2-4 2H12"/></svg></div>Hire a caregiver</div>
  <div class="abs step" style="left:921px;top:177px"><div class="step-icon"><svg width="40" height="40" viewBox="0 0 40 40" fill="none" stroke="#1fc1e0" stroke-width="3.5"><path d="M27 12c-2-3-13-4-13 3s13 4 13 11-11 6-14 2"/><path d="M20 4v32"/></svg></div>Pay for your care</div>
</section>

<section class="benefits">
  <h2 class="abs section-title" style="top:90px">Our benefits</h2>
  <div class="abs side-arrow" style="left:58px">‹</div>
  <div class="abs side-arrow" style="left:1128px">›</div>
  <div class="abs benefit" style="left:62px;top:176px">
    <svg width="40" height="44" viewBox="0 0 40 44" fill="none" stroke="#1fc1e0" stroke-width="2"><path d="M20 4v36"/><path d="M27 12c-2-3-13-4-13 3s13 4 13 11-11 6-14 2"/></svg>
    <h4>Reduced cost</h4><p>Nam libero tempore cum soluta nobis est eligendi optio cumque nihil impedit quo minus id quod maxime placeat</p>
  </div>
  <div class="abs benefit" style="left:436px;top:176px">
    <svg width="52" height="44" viewBox="0 0 52 44" fill="none" stroke="#1fc1e0" stroke-width="2"><circle cx="14" cy="9" r="5"/><circle cx="38" cy="9" r="5"/><circle cx="26" cy="22" r="4"/><path d="M6 40V22c0-4 16-4 16 0v18M30 40V22c0-4 16-4 16 0v18M21 40v-8c0-3 10-3 10 0v8"/></svg>
    <h4>Increased flexibility for parents</h4><p>Nam libero tempore cum soluta nobis est eligendi optio cumque nihil impedit quo minus id quod maxime placeat</p>
  </div>
  <div class="abs benefit" style="left:815px;top:176px">
    <svg width="44" height="44" viewBox="0 0 44 44" fill="none" stroke="#1fc1e0" stroke-width="2"><circle cx="22" cy="9" r="5"/><path d="M8 18l14 4 14-4M22 22v10l-8 10M22 32l8 10"/><path d="M6 6l6 6M38 6l-6 6"/></svg>
    <h4>Reduced illness</h4><p>Nam libero tempore cum soluta nobis est eligendi optio cumque nihil impedit quo minus id quod maxime placeat</p>
  </div>
  <span class="abs btn btn-pink">View more</span>
</section>

<footer class="site-footer">
  <div class="abs socials"><span class="social"></span><span class="social"></span><span class="social"></span><span class="social"></span><span class="social"></span><span class="social"></span></div>
  <div class="abs footer-nav">Home<span>/</span>About us<span>/</span>Services<span>/</span>How it works<span>/</span>FAQ<span>/</span>Contact us</div>
  <div class="abs copyright">© Copyright 2018 Bright Pram Hub. All Rights Reserved</div>
</footer>

</body>
</html>
```